TEBSIRK HOA Portal Site for Public

Clean up and organize current website; need website to look good and functional; this is a HOA (homeowner association management) website where homeowners can login and pay their bill, general information about a HOA, monthly newsletter page.
Competitors:
https://quillmarsh.example/
https://dorvinpalms.example/
https://www.kelbrookhomes.example/nevada
http://www.tpw-hoa.example/

Target Market(s)

homeowners

Industry/Entity Type

Real Estate

Coding

Coded - Design and coding required

Number of Pages Required

5+ page

Font styles to use
Serif

Colors
0292cd
33a6d7
e667a6
e34297

Requirements
Must have
• login to pay
• services page
• contact us
• order resale package
Nice to have
• page why an HOA would contract us

```html
<!DOCTYPE html>
<html lang="en">
<head>
<meta charset="utf-8">
<title>TEBSIRK – Homepage Variants</title>
<link href="https://fonts.googleapis.com/css2?family=Oswald:wght@300;400;500&family=Lato:wght@400;700&family=Roboto:wght@400&display=swap" rel="stylesheet">
<style>
:root{
  --blue:#0292cd;
  --blue-light:#33a6d7;
  --nav-blue:#1b8fd8;
  --pink:#e34297;
  --pink-soft:#e667a6;
  --ink:#1d1d1d;
  --text:#3b3b3b;
  --muted:#777;
  --gray-bg:#efefef;
  --bar-bg:#f2f2f2;
  --footer:#1e1e1e;
  --white:#fff;
}
*{box-sizing:border-box;margin:0;padding:0}
html,body{width:823px;height:1200px;overflow:hidden;background:var(--white)}
body{position:relative;font-family:"Lato",sans-serif;color:var(--text)}

.site{position:absolute;top:27px;width:712px;height:2220px;background:var(--white);
  transform:scale(.5144);transform-origin:0 0;overflow:hidden;box-shadow:0 0 14px rgba(0,0,0,.18)}
.site--a{left:27px}
.site--b{left:426px}
.abs{position:absolute}

/* top bar */
.topbar{position:absolute;top:0;left:0;width:100%;height:28px;background:var(--bar-bg)}
.topbar .social{position:absolute;left:488px;top:9px;display:flex;gap:15px}
.topbar .social i{display:block;width:10px;height:10px;border-radius:50%;background:#333}
.topbar .login{position:absolute;left:593px;top:0;height:28px;border-left:1px solid #ddd;padding-left:22px;
  font:300 12px/28px "Oswald",sans-serif;color:var(--pink)}

/* header */
.header{position:absolute;top:28px;left:0;width:100%;height:59px;background:var(--white)}
.brand{position:absolute;left:52px;top:18px;display:flex;align-items:center;gap:8px;
  font:500 18px/1 "Oswald",sans-serif;color:var(--ink);letter-spacing:1px}
.brand .mark{width:14px;height:14px;background:#5b9c34}
.contact-item{position:absolute;top:16px;display:flex;align-items:center;gap:10px;
  font:400 12px/1 "Oswald",sans-serif;color:#333}
.contact-item .ring{width:28px;height:28px;border:1px solid #c9d8e4;border-radius:50%;display:flex;align-items:center;justify-content:center}
.contact-item b{font-weight:500;color:var(--blue)}
.contact-item--mail{left:328px}
.contact-item--call{left:505px}

/* nav */
.nav{position:absolute;top:87px;left:0;width:100%;height:30px;background:var(--nav-blue);
  display:flex;justify-content:space-between;align-items:center;padding:0 20px 0 20px;
  font:400 11px/1 "Oswald",sans-serif;color:var(--white)}
.nav .current{opacity:.8}

/* hero */
.hero{position:absolute;top:117px;left:0;width:100%;height:320px}
.hero-photo{position:absolute;inset:0}
.hero-photo--park{background:linear-gradient(180deg,#3c3a34 0%,#4a5838 45%,#4f7a2e 72%,#3f6a25 100%)}
.hero-photo--town{background:linear-gradient(180deg,#c9d3e0 0%,#7d8796 35%,#4b5260 60%,#2e3a32 100%)}
.hero-title{position:absolute;top:58px;left:0;width:100%;text-align:center}
.hero-title .line1{display:block;font:400 38px/1.05 "Roboto",sans-serif}
.hero-title .line2{display:block;font:500 33px/1.2 "Oswald",sans-serif}
.site--a .hero-title{color:var(--white);text-shadow:0 2px 4px rgba(0,0,0,.45)}
.site--b .hero-title .line1{color:var(--pink)}
.site--b .hero-title .line2{color:var(--ink)}
.hero .btn{top:164px;left:298px}
.dots{position:absolute;top:274px;left:322px;display:flex;gap:12px}
.dots i{display:block;width:7px;height:7px;border-radius:50%;background:var(--white)}
.dots i.on{background:var(--blue-light)}

/* button */
.btn{position:absolute;height:30px;padding:0 16px 0 32px;background:var(--pink);color:var(--white);
  font:400 12px/30px "Oswald",sans-serif;letter-spacing:.3px;white-space:nowrap}
.btn::before{content:"";position:absolute;left:-12px;top:1px;width:28px;height:28px;border-radius:50%;
  background:var(--white);box-shadow:inset 0 0 0 3px var(--pink-soft)}
.btn--lg{font-size:14px;height:32px;line-height:32px;padding-left:36px}
.btn--lg::before{width:30px;height:30px;left:-14px}
.btn--sm{font-size:10px;height:26px;line-height:26px;padding:0 14px 0 30px}
.btn--sm::before{width:24px;height:24px;left:-10px}

/* about */
.about{position:absolute;top:437px;left:0;width:100%;height:268px;background:var(--white)}
.about h2,.section-title{font:500 28px/1 "Oswald",sans-serif;color:var(--ink)}
.about h2{position:absolute;left:52px;top:60px}
.about p{position:absolute;left:52px;top:108px;width:290px;font-size:11px;line-height:19px;color:#333}
.about .btn{left:64px;top:186px}
.about-frame{position:absolute;left:378px;top:-36px;width:294px;height:386px;z-index:3;
  clip-path:polygon(50% 0,100% 25%,100% 75%,50% 100%,0 75%,0 25%);background:var(--white)}
.about-photo{position:absolute;left:12px;top:14px;width:270px;height:358px;
  clip-path:polygon(50% 0,100% 25%,100% 75%,50% 100%,0 75%,0 25%);
  background:linear-gradient(160deg,#5d7fb6 0%,#a89a86 40%,#8a6a52 65%,#4f8a3a 100%)}

/* services */
.services{position:absolute;top:705px;left:0;width:100%;height:613px;background:var(--gray-bg)}
.services .section-title{position:absolute;top:50px;left:0;width:100%;text-align:center}
.service{position:absolute;width:156px;text-align:center}
.service .hex{margin:0 auto;width:134px;height:140px;clip-path:polygon(50% 0,100% 25%,100% 75%,50% 100%,0 75%,0 25%)}
.service .badge{position:absolute;left:50%;top:104px;margin-left:-32px;width:64px;height:64px;border-radius:50%;
  background:var(--white);display:flex;align-items:center;justify-content:center}
.service p{margin-top:26px;font-size:11px;line-height:16px;color:#2b2b2b}
.service.active p{color:var(--blue)}
.tone-1{background:linear-gradient(160deg,#4f5660,#8f8a84 55%,#3b3f45)}
.tone-2{background:linear-gradient(160deg,#6a6e72,#3a3a3c 55%,#8d8d8d)}
.tone-3{background:linear-gradient(160deg,#d9d7d3,#b8b2aa 55%,#e6e3df)}
.tone-4{background:linear-gradient(160deg,#b9b9b9,#9a9a9a 55%,#cfcfcf)}
.tone-5{background:linear-gradient(160deg,#9c9792,#6f6b66 55%,#c3beb8)}
.tone-6{background:linear-gradient(160deg,#4a4644,#2e2c2b 55%,#6d6965)}
.tone-7{background:linear-gradient(160deg,#d5d0c7,#a79a89 55%,#e4dfd8)}
.services .btn{top:518px;left:318px}

/* careers */
.careers{position:absolute;top:1318px;left:0;width:100%;height:168px;
  background:linear-gradient(180deg,#1b82cf 0%,#1876c2 100%);text-align:center;color:var(--white)}
.careers h3{position:absolute;top:28px;width:100%;font:300 20px/1 "Oswald",sans-serif}
.careers p{position:absolute;top:62px;left:70px;width:572px;font-size:11px;line-height:17px;opacity:.92}
.careers .btn{top:112px;left:318px}

/* events */
.events{position:absolute;top:1486px;left:0;width:100%;height:400px;background:var(--white)}
.events .section-title{position:absolute;top:57px;left:0;width:100%;text-align:center}
.event{position:absolute;top:102px;width:193px;height:225px;background:var(--white);box-shadow:0 2px 6px rgba(0,0,0,.13)}
.event .photo{height:104px;position:relative}
.photo--pool{background:linear-gradient(180deg,#6e8c5a 0%,#5a86a4 45%,#2ea3d0 70%,#8a8a86 100%)}
.photo--group{background:linear-gradient(180deg,#5e7d3c 0%,#a85a5a 45%,#3c4a78 75%,#6b8a3a 100%)}
.photo--grill{background:linear-gradient(180deg,#2f3440 0%,#4a4f5a 45%,#2b2b2d 75%,#6a6a68 100%)}
.date{position:absolute;left:6px;top:6px;width:34px;height:40px;background:var(--pink);color:var(--white);
  font:400 11px/13px "Oswald",sans-serif;text-align:center;padding-top:7px}
.event h4{margin:14px 7px 0;font:400 11px/16px "Oswald",sans-serif;color:var(--ink);text-transform:uppercase}
.event p{margin:8px 7px 0;font-size:9.5px;line-height:15.5px;color:#555}
.event a{display:block;margin:6px 7px 0;font-size:10px;color:var(--blue);text-decoration:none}

/* newsletter */
.newsletter{position:absolute;top:1888px;left:0;width:100%;height:92px;background:var(--pink-soft)}
.newsletter h5{position:absolute;left:117px;top:35px;font:500 14px/1 "Oswald",sans-serif;color:var(--white);letter-spacing:.3px}
.newsletter .field{position:absolute;left:303px;top:33px;width:264px;height:26px;background:var(--white);
  font-size:9px;line-height:26px;padding-left:10px;color:#666}
.newsletter .send{position:absolute;left:567px;top:33px;width:28px;height:26px;background:var(--blue);
  display:flex;align-items:center;justify-content:center}

/* footer */
.footer{position:absolute;top:1980px;left:0;width:100%;height:240px;background:var(--footer);color:#d8d8d8}
.fcol{position:absolute;top:32px}
.fcol h6{font:500 11px/1 "Oswald",sans-serif;color:var(--white);letter-spacing:.5px;margin-bottom:20px}
.fcol li{list-style:none;font-size:8.5px;line-height:18.5px}
.fcol h6.follow{margin-top:20px;margin-bottom:12px}
.fsocial{display:flex;gap:13px}
.fsocial i{display:block;width:8px;height:8px;border-radius:50%;background:var(--white)}
.copyright{position:absolute;top:205px;width:100%;text-align:center;font-size:8.5px;color:#cfcfcf}
</style>
</head>
<body>

<!-- Variant A -->
<div class="site site--a">
  <div class="topbar">
    <div class="social"><i></i><i></i><i></i><i></i></div>
    <div class="login">Homeowners Login</div>
  </div>
  <div class="header">
    <div class="brand"><span class="mark"></span>TEBSIRK</div>
    <div class="contact-item contact-item--mail"><span class="ring"><svg width="13" height="13" viewBox="0 0 24 24"><path d="M2 11 22 3 15 21 11 13Z" fill="none" stroke="#0292cd" stroke-width="2" stroke-linejoin="round"/></svg></span>Email Us : hello@tebsirk.example</div>
    <div class="contact-item contact-item--call"><span class="ring"><svg width="13" height="13" viewBox="0 0 24 24"><path d="M5 3h4l2 5-3 2a12 12 0 0 0 6 6l2-3 5 2v4a2 2 0 0 1-2 2A18 18 0 0 1 3 5a2 2 0 0 1 2-2Z" fill="none" stroke="#0292cd" stroke-width="2"/></svg></span>CALL : <b>+1 555-014-2270</b></div>
  </div>
  <nav class="nav">
    <span>Association Management</span><span>Southern Nevada</span><span>Services</span><span class="current">Homeowners</span><span>About Us</span><span>Leadership Team</span><span>Document Request</span><span>Pay Assessments</span><span>Contact</span>
  </nav>
  <section class="hero">
    <div class="hero-photo hero-photo--park" role="img" aria-label="Photo of neighbours at a community party on a lawn with a bounce house"></div>
    <h1 class="hero-title"><span class="line1">Southern Nevada</span><span class="line2">TEBSIRK Association Management</span></h1>
    <a class="btn btn--lg">Get Started &raquo;</a>
    <div class="dots"><i class="on"></i><i></i><i></i><i></i></div>
  </section>
  <section class="about">
    <h2>About Us</h2>
    <p>We are a full service community association management company. We believe in creating a sense of community for homeowners.</p>
    <a class="btn btn--sm">LOGIN TO PAY &raquo;</a>
    <div class="about-frame"><div class="about-photo" role="img" aria-label="Photo of a two-storey family house at dusk"></div></div>
  </section>
  <section class="services">
    <h2 class="section-title">What We Do</h2>
    <div class="service" style="left:43px;top:94px"><div class="hex tone-1" role="img" aria-label="Photo of smiling association managers"></div><span class="badge"><svg width="26" height="26" viewBox="0 0 24 24" fill="none" stroke="#8a6fd1" stroke-width="1.4"><circle cx="9" cy="8" r="3"/><path d="M3 20c0-4 3-6 6-6s6 2 6 6"/><circle cx="17" cy="9" r="2.5" stroke="#e34297"/></svg></span><p>Accessible, licensed<br>Association Managers</p></div>
    <div class="service" style="left:200px;top:94px"><div class="hex tone-2" role="img" aria-label="Photo of a hand holding a phone"></div><span class="badge"><svg width="26" height="26" viewBox="0 0 24 24" fill="none" stroke="#8a6fd1" stroke-width="1.4"><rect x="4" y="4" width="12" height="16" rx="2"/><circle cx="17" cy="8" r="4" stroke="#e34297"/></svg></span><p>24 hour<br>emergency service</p></div>
    <div class="service active" style="left:356px;top:94px"><div class="hex tone-3" role="img" aria-label="Photo of a laptop with financial reports"></div><span class="badge"><svg width="26" height="26" viewBox="0 0 24 24" fill="none" stroke="#8a6fd1" stroke-width="1.4"><rect x="4" y="3" width="16" height="18" rx="1"/><path d="M7 16l3-4 3 2 4-5" stroke="#e34297"/></svg></span><p>Provide monthly financial<br>reports to the Board of Directors</p></div>
    <div class="service" style="left:513px;top:94px"><div class="hex tone-4" role="img" aria-label="Photo of a hand using a tablet"></div><span class="badge"><svg width="26" height="26" viewBox="0 0 24 24" fill="none" stroke="#8a6fd1" stroke-width="1.4"><rect x="3" y="6" width="14" height="10" rx="1"/><path d="M7 19h6"/><circle cx="18" cy="6" r="2.5" stroke="#e34297"/></svg></span><p>24 hour Web site access:<br>online account information</p></div>
    <div class="service" style="left:122px;top:310px"><div class="hex tone-5" role="img" aria-label="Photo of hands using a calculator"></div><span class="badge"><svg width="26" height="26" viewBox="0 0 24 24" fill="none" stroke="#8a6fd1" stroke-width="1.4"><rect x="5" y="4" width="14" height="17" rx="1"/><path d="M9 13l2 2 4-4" stroke="#e34297"/></svg></span><p>Prepare the annual budget<br>for Board approval</p></div>
    <div class="service" style="left:279px;top:310px"><div class="hex tone-6" role="img" aria-label="Photo of a business handshake"></div><span class="badge"><svg width="26" height="26" viewBox="0 0 24 24" fill="none" stroke="#8a6fd1" stroke-width="1.4"><path d="M2 12l5-4 5 3 5-3 5 4-5 5H7Z"/><path d="M9 13l3 2" stroke="#e34297"/></svg></span><p>Prepare for and attend the<br>budget ratification meeting</p></div>
    <div class="service" style="left:435px;top:310px"><div class="hex tone-7" role="img" aria-label="Photo of a desk with calendar and coffee"></div><span class="badge"><svg width="26" height="26" viewBox="0 0 24 24" fill="none" stroke="#8a6fd1" stroke-width="1.4"><rect x="4" y="5" width="16" height="15" rx="1"/><path d="M4 9h16M8 3v4M16 3v4" /><path d="M8 13h2M12 13h2M16 13h1M8 16h2M12 16h2" stroke="#e34297"/></svg></span><p>Preparation and scheduling<br>for Board meetings and annual<br>membership meetings</p></div>
    <a class="btn btn--sm">VIEW ALL &raquo;</a>
  </section>
  <section class="careers">
    <h3>Careers at TEBSIRK Association Management</h3>
    <p>I aim high. I own it. I am genuinely helpful. I do what's right. I build great relationships. I make people's lives, homes and communities better.&nbsp; I am TEBSIRK Association Management, and I am ready to make a difference, every day.</p>
    <a class="btn btn--sm">JOIN NOW &raquo;</a>
  </section>
  <section class="events">
    <h2 class="section-title">Events</h2>
    <article class="event" style="left:55px"><div class="photo photo--pool" role="img" aria-label="Photo of a community swimming pool"><span class="date">FEB<br>15</span></div><h4>Sed ut perspiciatis unde omnis<br>iste natus</h4><p>Lorem ipsum dolor sit amet, consectetur adipiscing elit, sed do eiusmod tempor incididunt ut labore et dolore</p><a>Read More &raquo;</a></article>
    <article class="event" style="left:260px"><div class="photo photo--group" role="img" aria-label="Photo of residents at an outdoor event"><span class="date">FEB<br>15</span></div><h4>Sed ut perspiciatis unde omnis<br>iste natus</h4><p>Lorem ipsum dolor sit amet, consectetur adipiscing elit, sed do eiusmod tempor incididunt ut labore et dolore</p><a>Read More &raquo;</a></article>
    <article class="event" style="left:465px"><div class="photo photo--grill" role="img" aria-label="Photo of a barbecue grill at a cookout"><span class="date">FEB<br>15</span></div><h4>Sed ut perspiciatis unde omnis<br>iste natus</h4><p>Lorem ipsum dolor sit amet, consectetur adipiscing elit, sed do eiusmod tempor incididunt ut labore et dolore</p><a>Read More &raquo;</a></article>
  </section>
  <section class="newsletter">
    <h5>SIGN UP OUR NEWSLETTER</h5>
    <div class="field">Email Address</div>
    <div class="send"><svg width="13" height="13" viewBox="0 0 24 24"><path d="M2 11 22 3 15 21 11 13Z" fill="none" stroke="#fff" stroke-width="2" stroke-linejoin="round"/></svg></div>
  </section>
  <footer class="footer">
    <div class="fcol" style="left:52px"><h6>COMPANY</h6><ul><li>Association Management</li><li>Southern Nevada</li><li>Services</li><li>Homeowners</li><li>About Us</li></ul></div>
    <div class="fcol" style="left:220px"><h6>LEGAL</h6><ul><li>Leadership Team</li><li>Document Request</li><li>Pay Assessments</li><li>Contact</li></ul></div>
    <div class="fcol" style="left:369px"><h6>CONTACT</h6><ul><li>TEBSIRK Association Management</li><li>1 555-014-2270</li><li>hello@tebsirk.example</li></ul></div>
    <div class="fcol" style="left:588px"><h6>MY ACCOUNT</h6><ul><li>Homeowner Login</li><li>Login to Pay</li></ul><h6 class="follow">FOLLOW US</h6><div class="fsocial"><i></i><i></i><i></i><i></i></div></div>
    <p class="copyright">© 2019 The Company name. All rights Reserved.Privacy Policy | Terms Of Use</p>
  </footer>
</div>

<!-- Variant B -->
<div class="site site--b">
  <div class="topbar">
    <div class="social"><i></i><i></i><i></i><i></i></div>
    <div class="login">Homeowners Login</div>
  </div>
  <div class="header">
    <div class="brand"><span class="mark"></span>TEBSIRK</div>
    <div class="contact-item contact-item--mail"><span class="ring"><svg width="13" height="13" viewBox="0 0 24 24"><path d="M2 11 22 3 15 21 11 13Z" fill="none" stroke="#0292cd" stroke-width="2" stroke-linejoin="round"/></svg></span>Email Us : hello@tebsirk.example</div>
    <div class="contact-item contact-item--call"><span class="ring"><svg width="13" height="13" viewBox="0 0 24 24"><path d="M5 3h4l2 5-3 2a12 12 0 0 0 6 6l2-3 5 2v4a2 2 0 0 1-2 2A18 18 0 0 1 3 5a2 2 0 0 1 2-2Z" fill="none" stroke="#0292cd" stroke-width="2"/></svg></span>CALL : <b>+1 555-014-2270</b></div>
  </div>
  <nav class="nav">
    <span>Association Management</span><span>Southern Nevada</span><span>Services</span><span class="current">Homeowners</span><span>About Us</span><span>Leadership Team</span><span>Document Request</span><span>Pay Assessments</span><span>Contact</span>
  </nav>
  <section class="hero">
    <div class="hero-photo hero-photo--town" role="img" aria-label="Photo of a mountain town with snowy peaks"></div>
    <h1 class="hero-title"><span class="line1">Southern Nevada</span><span class="line2">TEBSIRK Association Management</span></h1>
    <a class="btn btn--lg">Get Started &raquo;</a>
    <div class="dots"><i class="on"></i><i></i><i></i><i></i></div>
  </section>
  <section class="about">
    <h2>About Us</h2>
    <p>We are a full service community association management company. We believe in creating a sense of community for homeowners.</p>
    <a class="btn btn--sm">LOGIN TO PAY &raquo;</a>
    <div class="about-frame"><div class="about-photo" role="img" aria-label="Photo of a two-storey family house at dusk"></div></div>
  </section>
  <section class="services">
    <h2 class="section-title">What We Do</h2>
    <div class="service" style="left:43px;top:94px"><div class="hex tone-1" role="img" aria-label="Photo of smiling association managers"></div><span class="badge"><svg width="26" height="26" viewBox="0 0 24 24" fill="none" stroke="#8a6fd1" stroke-width="1.4"><circle cx="9" cy="8" r="3"/><path d="M3 20c0-4 3-6 6-6s6 2 6 6"/><circle cx="17" cy="9" r="2.5" stroke="#e34297"/></svg></span><p>Accessible, licensed<br>Association Managers</p></div>
    <div class="service" style="left:200px;top:94px"><div class="hex tone-2" role="img" aria-label="Photo of a hand holding a phone"></div><span class="badge"><svg width="26" height="26" viewBox="0 0 24 24" fill="none" stroke="#8a6fd1" stroke-width="1.4"><rect x="4" y="4" width="12" height="16" rx="2"/><circle cx="17" cy="8" r="4" stroke="#e34297"/></svg></span><p>24 hour<br>emergency service</p></div>
    <div class="service active" style="left:356px;top:94px"><div class="hex tone-3" role="img" aria-label="Photo of a laptop with financial reports"></div><span class="badge"><svg width="26" height="26" viewBox="0 0 24 24" fill="none" stroke="#8a6fd1" stroke-width="1.4"><rect x="4" y="3" width="16" height="18" rx="1"/><path d="M7 16l3-4 3 2 4-5" stroke="#e34297"/></svg></span><p>Provide monthly financial<br>reports to the Board of Directors</p></div>
    <div class="service" style="left:513px;top:94px"><div class="hex tone-4" role="img" aria-label="Photo of a hand using a tablet"></div><span class="badge"><svg width="26" height="26" viewBox="0 0 24 24" fill="none" stroke="#8a6fd1" stroke-width="1.4"><rect x="3" y="6" width="14" height="10" rx="1"/><path d="M7 19h6"/><circle cx="18" cy="6" r="2.5" stroke="#e34297"/></svg></span><p>24 hour Web site access:<br>online account information</p></div>
    <div class="service" style="left:122px;top:310px"><div class="hex tone-5" role="img" aria-label="Photo of hands using a calculator"></div><span class="badge"><svg width="26" height="26" viewBox="0 0 24 24" fill="none" stroke="#8a6fd1" stroke-width="1.4"><rect x="5" y="4" width="14" height="17" rx="1"/><path d="M9 13l2 2 4-4" stroke="#e34297"/></svg></span><p>Prepare the annual budget<br>for Board approval</p></div>
    <div class="service" style="left:279px;top:310px"><div class="hex tone-6" role="img" aria-label="Photo of a business handshake"></div><span class="badge"><svg width="26" height="26" viewBox="0 0 24 24" fill="none" stroke="#8a6fd1" stroke-width="1.4"><path d="M2 12l5-4 5 3 5-3 5 4-5 5H7Z"/><path d="M9 13l3 2" stroke="#e34297"/></svg></span><p>Prepare for and attend the<br>budget ratification meeting</p></div>
    <div class="service" style="left:435px;top:310px"><div class="hex tone-7" role="img" aria-label="Photo of a desk with calendar and coffee"></div><span class="badge"><svg width="26" height="26" viewBox="0 0 24 24" fill="none" stroke="#8a6fd1" stroke-width="1.4"><rect x="4" y="5" width="16" height="15" rx="1"/><path d="M4 9h16M8 3v4M16 3v4" /><path d="M8 13h2M12 13h2M16 13h1M8 16h2M12 16h2" stroke="#e34297"/></svg></span><p>Preparation and scheduling<br>for Board meetings and annual<br>membership meetings</p></div>
    <a class="btn btn--sm">VIEW ALL &raquo;</a>
  </section>
  <section class="careers">
    <h3>Careers at TEBSIRK Association Management</h3>
    <p>I aim high. I own it. I am genuinely helpful. I do what's right. I build great relationships. I make people's lives, homes and communities better.&nbsp; I am TEBSIRK Association Management, and I am ready to make a difference, every day.</p>
    <a class="btn btn--sm">JOIN NOW &raquo;</a>
  </section>
  <section class="events">
    <h2 class="section-title">Events</h2>
    <article class="event" style="left:55px"><div class="photo photo--pool" role="img" aria-label="Photo of a community swimming pool"><span class="date">FEB<br>15</span></div><h4>Sed ut perspiciatis unde omnis<br>iste natus</h4><p>Lorem ipsum dolor sit amet, consectetur adipiscing elit, sed do eiusmod tempor incididunt ut labore et dolore</p><a>Read More &raquo;</a></article>
    <article class="event" style="left:260px"><div class="photo photo--group" role="img" aria-label="Photo of residents at an outdoor event"><span class="date">FEB<br>15</span></div><h4>Sed ut perspiciatis unde omnis<br>iste natus</h4><p>Lorem ipsum dolor sit amet, consectetur adipiscing elit, sed do eiusmod tempor incididunt ut labore et dolore</p><a>Read More &raquo;</a></article>
    <article class="event" style="left:465px"><div class="photo photo--grill" role="img" aria-label="Photo of a barbecue grill at a cookout"><span class="date">FEB<br>15</span></div><h4>Sed ut perspiciatis unde omnis<br>iste natus</h4><p>Lorem ipsum dolor sit amet, consectetur adipiscing elit, sed do eiusmod tempor incididunt ut labore et dolore</p><a>Read More &raquo;</a></article>
  </section>
  <section class="newsletter">
    <h5>SIGN UP OUR NEWSLETTER</h5>
    <div class="field">Email Address</div>
    <div class="send"><svg width="13" height="13" viewBox="0 0 24 24"><path d="M2 11 22 3 15 21 11 13Z" fill="none" stroke="#fff" stroke-width="2" stroke-linejoin="round"/></svg></div>
  </section>
  <footer class="footer">
    <div class="fcol" style="left:52px"><h6>COMPANY</h6><ul><li>Association Management</li><li>Southern Nevada</li><li>Services</li><li>Homeowners</li><li>About Us</li></ul></div>
    <div class="fcol" style="left:220px"><h6>LEGAL</h6><ul><li>Leadership Team</li><li>Document Request</li><li>Pay Assessments</li><li>Contact</li></ul></div>
    <div class="fcol" style="left:369px"><h6>CONTACT</h6><ul><li>TEBSIRK Association Management</li><li>1 555-014-2270</li><li>hello@tebsirk.example</li></ul></div>
    <div class="fcol" style="left:588px"><h6>MY ACCOUNT</h6><ul><li>Homeowner Login</li><li>Login to Pay</li></ul><h6 class="follow">FOLLOW US</h6><div class="fsocial"><i></i><i></i><i></i><i></i></div></div>
    <p class="copyright">© 2019 The Company name. All rights Reserved.Privacy Policy | Terms Of Use</p>
  </footer>
</div>

</body>
</html>
```